Business Cards for a law firm

Business cards for our law firm. Use our silhoette logo and OAK PARTNERS - check our website (www.oakpartners.example)

Contact Information for Business Card

our silhouette logo, OAK PARTNERS, 800-555-0147, Dorian Pemberton, dorian@oakpartners.example

Requirements
Must have
• our silhouette logo, OAK PARTNERS, 800-555-0147, Dorian Pemberton, dorian@oakpartners.example

```html
<!DOCTYPE html>
<html lang="en">
<head>
<meta charset="utf-8">
<title>Oak Partners – Business Cards</title>
<link href="https://fonts.googleapis.com/css2?family=Montserrat:wght@400;500;700;800&display=swap" rel="stylesheet">
<style>
  :root {
    --navy: #2b3566;
    --navy-deep: #232c58;
    --navy-soft: #3b4680;
    --orange: #f6a81c;
    --white: #ffffff;
    --bg: #e9e9ec;
  }
  * { box-sizing: border-box; margin: 0; padding: 0; }
  html, body { width: 1200px; height: 856px; overflow: hidden; }
  body {
    background: var(--bg);
    font-family: "Montserrat", sans-serif;
    position: relative;
  }
  .card {
    position: absolute;
    width: 525px;
    height: 300px;
    overflow: hidden;
    background: var(--navy);
    color: var(--white);
    box-shadow: 0 6px 18px rgba(0,0,0,.18);
  }
  .card--front { left: 337px; top: 90px; }
  .card--back  { left: 337px; top: 466px; }
  .office-backdrop {
    position: absolute; inset: 0;
    background: linear-gradient(160deg, var(--navy) 0%, var(--navy-soft) 55%, var(--navy-deep) 100%);
  }
  .logo {
    position: absolute;
    display: flex; align-items: center; gap: 8px;
    font-weight: 800; letter-spacing: 1px; color: var(--white);
    white-space: nowrap;
  }
  .logo__dot {
    width: 22px; height: 22px; border-radius: 50%;
    background: var(--white);
  }
  .card--front .logo { left: 22px; top: 18px; font-size: 24px; }

  .headline { position: absolute; left: 192px; top: 58px; width: 172px; }
  .headline__brand { color: var(--orange); font-weight: 800; font-size: 12px; letter-spacing: .4px; white-space: nowrap; }
  .headline__title { font-weight: 800; font-size: 14px; line-height: 1.25; margin-top: 5px; }
  .headline__stat { font-weight: 400; font-size: 10.5px; line-height: 1.35; margin-top: 6px; white-space: nowrap; }
  .cta {
    display: inline-block; margin-top: 8px;
    background: var(--orange); color: var(--navy-deep);
    font-weight: 800; font-size: 8px; white-space: nowrap;
    padding: 7px 9px; border-radius: 12px;
  }

  .portrait { position: absolute; background: linear-gradient(180deg, #4a5275 0%, #262b45 100%); }
  .portrait--left  { left: 0; top: 168px; width: 182px; height: 108px; }
  .portrait--right { left: 372px; top: 18px; width: 153px; height: 212px; }

  .ribbon { position: absolute; inset: 0; }
  .ribbon-label {
    position: absolute; display: flex; align-items: center; gap: 6px;
    color: var(--navy-deep); font-weight: 500; font-size: 10px; white-space: nowrap;
  }
  .ribbon-label__icon {
    width: 12px; height: 12px; border-radius: 50%;
    background: var(--navy); border: 2px solid var(--orange);
    box-shadow: 0 0 0 1px var(--navy);
  }
  .ribbon-label--left  { left: 16px;  top: 282px; }
  .ribbon-label--mid   { left: 210px; top: 256px; }
  .ribbon-label--right { left: 388px; top: 235px; }

  .card--back .logo { left: 0; right: 0; justify-content: center; top: 40px; font-size: 28px; }
  .contact {
    position: absolute; left: 0; right: 0; top: 96px;
    text-align: center;
  }
  .contact__name { font-weight: 800; font-size: 20px; letter-spacing: .5px; }
  .contact__icon { display: block; margin: 6px auto 1px; }
  .contact__line { font-size: 13px; font-weight: 400; letter-spacing: .3px; }
  .back-stripe {
    position: absolute; left: 0; right: 0; bottom: 0; height: 26px;
    background: var(--orange);
  }
</style>
</head>
<body>

<section class="card card--front">
  <div class="office-backdrop" role="img" aria-label="Faint photo of a modern office interior in navy tones"></div>

  <div class="logo"><span class="logo__dot"></span>OAK PARTNERS</div>

  <div class="headline">
    <p class="headline__brand">THE OAK PARTNERS®</p>
    <p class="headline__title">INJURED?<br>CALL THE OAK<br>PARTNERS!</p>
    <p class="headline__stat">Over $400,000,000<br>Recovered For Our Clients.</p>
    <span class="cta">GET A FREE CONSULTATION NOW</span>
  </div>

  <div class="portrait portrait--left" role="img" aria-label="Portrait photo of a smiling attorney in a dark suit"></div>
  <div class="portrait portrait--right" role="img" aria-label="Portrait photo of a second attorney in a dark suit and tie"></div>

  <svg class="ribbon" width="525" height="300" viewBox="0 0 525 300" aria-hidden="true">
    <polygon fill="#f6a81c" points="0,276 184,276 200,250 362,250 374,230 525,230 525,252 382,252 370,274 208,274 192,300 0,300"/>
  </svg>

  <div class="ribbon-label ribbon-label--left"><span class="ribbon-label__icon"></span>Free Consultation</div>
  <div class="ribbon-label ribbon-label--mid"><span class="ribbon-label__icon"></span>No Fee Unless You Win</div>
  <div class="ribbon-label ribbon-label--right"><span class="ribbon-label__icon"></span>We'll Come To You</div>
</section>

<section class="card card--back">
  <div class="office-backdrop" role="img" aria-label="Faint photo of a modern office interior in navy tones"></div>

  <div class="logo"><span class="logo__dot"></span>OAK PARTNERS</div>

  <div class="contact">
    <p class="contact__name">DORIAN PEMBERTON</p>
    <svg class="contact__icon" width="14" height="12" viewBox="0 0 14 12" aria-hidden="true">
      <path fill="#fff" d="M1 3 C4 0 10 0 13 3 L11 5 L9 3.5 L5 3.5 L3 5 Z M3 6 L11 6 L12 11 L2 11 Z"/>
    </svg>
    <p class="contact__line">800-555-0147</p>
    <svg class="contact__icon" width="14" height="10" viewBox="0 0 14 10" aria-hidden="true">
      <rect x="0.5" y="0.5" width="13" height="9" fill="#fff"/>
      <path d="M0.5 0.5 L7 6 L13.5 0.5" fill="none" stroke="#2b3566" stroke-width="1.2"/>
    </svg>
    <p class="contact__line">dorian@oakpartners.example</p>
    <svg class="contact__icon" width="13" height="13" viewBox="0 0 13 13" aria-hidden="true">
      <circle cx="6.5" cy="6.5" r="6" fill="#fff"/>
      <ellipse cx="6.5" cy="6.5" rx="2.6" ry="6" fill="none" stroke="#2b3566" stroke-width=".9"/>
      <line x1="0.5" y1="6.5" x2="12.5" y2="6.5" stroke="#2b3566" stroke-width=".9"/>
    </svg>
    <p class="contact__line">www.oakpartners.example</p>
  </div>

  <div class="back-stripe"></div>
</section>

</body>
</html>
```